Brochure Design Project

We are looking for a company brochure that is no more than 10 pages. If should contain information on our company (we will provide), management, financial data and product information. We will provide all this data. At this point we are just looking for some ideas on design and layout. Our company is an insurance company that sell homeowners insurance and other products. You can learn more about the company at larkmoorcover.com.
Target Market(s)
Insurance Agents
Industry/Entity Type
Financial
Look and feel

```html
<!DOCTYPE html>
<html lang="en">
<head>
<meta charset="utf-8">
<title>Larkmoor Cover — Brochure Spread</title>
<link rel="stylesheet" href="https://fonts.googleapis.com/css2?family=Source+Sans+3:wght@400;500&family=Arimo&family=Tinos&display=swap">
<style>
  :root {
    --page: #ffffff;
    --ink-blue: #1d3f97;
    --body-blue: #3a5aa8;
    --table-ink: #55555c;
    --bar-light: #d9dcf0;
    --bar-dark: #5a5aa8;
    --frame: #3a3a3a;
    --rule: #c9cbe0;
  }
  * { margin: 0; padding: 0; box-sizing: border-box; }
  html, body { width: 1200px; height: 900px; overflow: hidden; background: var(--page); }
  .canvas { position: relative; width: 1200px; height: 900px; }

  .spread {
    position: absolute; left: 107px; top: 63px; width: 983px; height: 695px;
    border: 1px solid var(--frame); overflow: hidden;
  }
  .spread-photo {
    position: absolute; inset: 0;
    background:
      radial-gradient(ellipse 180px 260px at 700px 430px, rgba(224,120,170,.55), transparent 70%),
      radial-gradient(ellipse 220px 380px at 800px 360px, rgba(226,110,165,.6), transparent 70%),
      radial-gradient(ellipse 150px 300px at 160px 380px, rgba(200,206,214,.7), transparent 70%),
      radial-gradient(ellipse 120px 180px at 360px 470px, rgba(190,196,205,.6), transparent 70%),
      linear-gradient(180deg, #f4f4f4 0%, #ececec 45%, #e6e2e4 100%);
  }
  .spread-veil { position: absolute; inset: 0; background: rgba(255,255,255,.35); }
  .swoosh { position: absolute; inset: 0; }

  .title { position: absolute; left: 53px; top: 52px; color: var(--ink-blue); font-family: "Source Sans 3", sans-serif; }
  .title-kicker { display: block; margin-left: 47px; font-size: 19px; line-height: 20px; }
  .title-main { display: block; font-size: 47px; line-height: 44px; font-weight: 400; letter-spacing: -.3px; }

  .intro { position: absolute; top: 154px; width: 210px; font-family: "Source Sans 3", sans-serif;
    font-size: 10px; line-height: 12.7px; color: var(--body-blue); }
  .intro p + p { margin-top: 12.7px; }
  .intro-a { left: 30px; }
  .intro-b { left: 250px; width: 196px; }

  .statement { position: absolute; border-collapse: collapse; table-layout: fixed;
    font-family: "Arimo", sans-serif; font-size: 7.4px; color: var(--table-ink); }
  .statement td, .statement th { height: 12.85px; padding: 0 0 0 5px; text-align: left; font-weight: 400; white-space: nowrap; vertical-align: middle; }
  .statement .head th { background: linear-gradient(90deg, var(--bar-light) 0%, #c4c6e6 60%, var(--bar-dark) 100%); height: 13px; }
  .statement .units td { height: 15px; }
  .statement .gap td { height: 8px; }
  .statement .wrap td { white-space: normal; line-height: 8px; height: 16px; }

  .statement-left { left: 30px; top: 342px; width: 431px; }
  .statement-right { left: 518px; top: 152px; width: 460px; }

  .folio-rule { position: absolute; top: 654px; height: 1px; background: var(--rule); }
  .folio-rule.left { left: 30px; width: 430px; }
  .folio-rule.right { left: 520px; width: 360px; }
  .folio-url { position: absolute; left: 884px; top: 650px; font-family: "Tinos", serif; font-size: 6px; color: #9a9aa4; }
</style>
</head>
<body>
<div class="canvas">
  <section class="spread">
    <div class="spread-photo" role="img" aria-label="Family of four outside their home, holding a pink piggy bank together"></div>
    <div class="spread-veil"></div>
    <svg class="swoosh" width="983" height="695" viewBox="0 0 983 695" aria-hidden="true">
      <path d="M0 360 C 200 300, 420 300, 620 340 C 760 370, 880 430, 983 520 L 983 695 L 940 695 C 860 560, 700 470, 520 440 C 330 410, 150 420, 0 470 Z" fill="rgba(255,255,255,.45)"/>
      <path d="M0 560 C 180 510, 380 520, 520 600 C 560 625, 590 660, 610 695 L 0 695 Z" fill="rgba(255,255,255,.4)"/>
      <line x1="491" y1="0" x2="491" y2="695" stroke="rgba(255,255,255,.5)"/>
    </svg>

    <h1 class="title">
      <span class="title-kicker">Protecting your</span>
      <span class="title-main">Most precious.</span>
    </h1>

    <div class="intro intro-a">
      <p>Lorem ipsum dolor sit amet, consectetuer adipiscing elit. Aenean commodo ligula eget dolor. Aenean massa. Cum sociis</p>
      <p>&nbsp;natoque penatibus et magnis dis parturient montes, nascetur ridiculus mus. Donec quam felis, ultricies nec, pellentesque eu, pretium quis, sem. Nulla consequat massa quis enim. Donec pede justo, fringilla vel, aliquet nec, vulputate eget, arcu. In enim justo, rhoncus ut, imperdiet a, venenatis vitae, justo. Nullam dictum felis eu pede mollis</p>
    </div>
    <div class="intro intro-b">
      <p>pretium. Integer tincidunt. Cras dapibus. Vivamus elementum semper nisi. Aenean vulputate eleifend tellus. Aenean leo ligula, porttitor eu, consequat vitae, eleifend ac, enim. Aliquam lorem ante, dapibus in, viverra quis, feugiat a, tellus. Phasellus viverra nulla ut metus varius laoreet. Quisque rutrum. Aenean imperdiet. Etiam ultricies nisi vel augue. Curabitur ullamcorper ultricies nisi. Nam eget dui. Etiam rhoncus. Maecenas tempus, tellus eget condimentum rhoncus, sem quam semper.</p>
    </div>

    <table class="statement statement-left">
      <colgroup><col style="width:146px"><col style="width:62px"><col style="width:62px"><col style="width:48px"><col style="width:48px"><col style="width:65px"></colgroup>
      <tr class="head"><th>Management Income Statement</th><th>2008</th><th></th><th>2007</th><th></th><th>+/- %</th></tr>
      <tr class="units"><td></td><td></td><td>€ million</td><td>%</td><td>€ million</td><td>%</td></tr>
      <tr class="gap"><td colspan="6"></td></tr>
      <tr><td>Consolidated Sales</td><td>1,530.3</td><td>100.0%</td><td>1,274.0</td><td>100.0%</td><td>20.1%</td></tr>
      <tr><td>Cost of material</td><td>736.4</td><td>48.1%</td><td>654.0</td><td>51.3%</td><td>12.6%</td></tr>
      <tr><td>Gross profit</td><td>794.0</td><td>51.9%</td><td>620.0</td><td>48.7%</td><td>28.1%</td></tr>
      <tr><td>Royalty and commission income</td><td>43.7</td><td>51.9%</td><td>40.3</td><td>3.2%</td><td>8.3%</td></tr>
      <tr><td colspan="6">Selling, general and administrative expenses</td></tr>
      <tr><td>Marketing/Retail expenses</td><td>214.6</td><td>14.0%</td><td>163.9</td><td>12.9%</td><td>30.9%</td></tr>
      <tr><td>Research, design and developement</td><td>36.9</td><td>2.4%</td><td>29.9</td><td>2.3%</td><td>23.3%</td></tr>
      <tr><td>Other expenses</td><td>202.0</td><td>13.2%</td><td>183.3</td><td>14.4%</td><td>10.2%</td></tr>
      <tr><td>Total</td><td>453.4</td><td>29.6%</td><td>377.1</td><td>29.6%</td><td>20.2%</td></tr>
      <tr><td>EBITDA</td><td>384.2</td><td>25.1%</td><td>283.3</td><td>22.2%</td><td>35.6%</td></tr>
      <tr><td>Depreciation</td><td>19.3</td><td>1.3%</td><td>20.1</td><td>1.6%</td><td>-4.1%</td></tr>
      <tr><td>EBIT</td><td>365.0</td><td>23.9%</td><td>263.2</td><td>20.7%</td><td>38.7%</td></tr>
      <tr><td>Financial result</td><td>5.7</td><td>0.4%</td><td>0.9</td><td>0.1%</td><td>540.7%</td></tr>
      <tr><td>EBT</td><td>370.7</td><td>24.2%</td><td>264.1</td><td>20.7%</td><td>40.4%</td></tr>
      <tr><td>Income taxes</td><td>111.7</td><td>7.3%</td><td>84.2</td><td>6.6%</td><td>32.6%</td></tr>
      <tr><td>Tax rate</td><td>30.1%</td><td></td><td>31.9%</td><td></td><td></td></tr>
    </table>

    <table class="statement statement-right">
      <colgroup><col style="width:148px"><col style="width:62px"><col style="width:62px"><col style="width:49px"><col style="width:47px"><col style="width:92px"></colgroup>
      <tr class="head"><th>Management Income Statement</th><th>2008</th><th></th><th>2007</th><th></th><th>+/- %</th></tr>
      <tr class="units"><td></td><td></td><td>€ million</td><td>%</td><td>€ million</td><td>%</td></tr>
      <tr class="gap"><td colspan="6"></td></tr>
      <tr><td>Consolidated Sales</td><td>1,530.3</td><td>100.0%</td><td>1,274.0</td><td>100.0%</td><td>20.1%</td></tr>
      <tr><td>Cost of material</td><td>736.4</td><td>48.1%</td><td>654.0</td><td>51.3%</td><td>12.6%</td></tr>
      <tr><td>Gross profit</td><td>794.0</td><td>51.9%</td><td>620.0</td><td>48.7%</td><td>28.1%</td></tr>
      <tr><td>Royalty and commission income</td><td>43.7</td><td>51.9%</td><td>40.3</td><td>3.2%</td><td>8.3%</td></tr>
      <tr><td colspan="6">Selling, general and administrative expenses</td></tr>
      <tr><td>Marketing/Retail expenses</td><td>214.6</td><td>14.0%</td><td>163.9</td><td>12.9%</td><td>30.9%</td></tr>
      <tr><td>Research, design and developement</td><td>36.9</td><td>2.4%</td><td>29.9</td><td>2.3%</td><td>23.3%</td></tr>
      <tr><td>Other expenses</td><td>202.0</td><td>13.2%</td><td>183.3</td><td>14.4%</td><td>10.2%</td></tr>
      <tr><td>Total</td><td>453.4</td><td>29.6%</td><td>377.1</td><td>29.6%</td><td>20.2%</td></tr>
      <tr><td>EBITDA</td><td>384.2</td><td>25.1%</td><td>283.3</td><td>22.2%</td><td>35.6%</td></tr>
      <tr><td>Depreciation</td><td>19.3</td><td>1.3%</td><td>20.1</td><td>1.6%</td><td>-4.1%</td></tr>
      <tr><td>EBIT</td><td>365.0</td><td>23.9%</td><td>263.2</td><td>20.7%</td><td>38.7%</td></tr>
      <tr><td>Financial result</td><td>5.7</td><td>0.4%</td><td>0.9</td><td>0.1%</td><td>540.7%</td></tr>
      <tr><td>EBT</td><td>370.7</td><td>24.2%</td><td>264.1</td><td>20.7%</td><td>40.4%</td></tr>
      <tr><td>Income taxes</td><td>111.7</td><td>7.3%</td><td>84.2</td><td>6.6%</td><td>32.6%</td></tr>
      <tr><td>Tax rate</td><td>30.1%</td><td></td><td>31.9%</td><td></td><td></td></tr>
      <tr><td>Minority interests</td><td>-1.7</td><td>-0.1%</td><td>-0.6</td><td>0.0%</td><td></td></tr>
      <tr><td>Net earnings</td><td>257.3</td><td>16.8%</td><td>179.3</td><td>14.1%</td><td>43.5%</td></tr>
      <tr><td>Weighted average shares outstanding (million)</td><td>16.025</td><td></td><td>15.932</td><td></td><td>0.6%</td></tr>
      <tr class="wrap"><td>Weighted average shares outstanding, diluted (million)</td><td>16.353</td><td></td><td>16.449</td><td></td><td>-0.6%</td></tr>
      <tr><td>Earnings per share in €</td><td>16.06</td><td></td><td>11.26</td><td></td><td>42.7%</td></tr>
      <tr><td>Earnings per share, diluted in €</td><td>15.74</td><td></td><td>10.90</td><td></td><td>44.3%</td></tr>
    </table>

    <div class="folio-rule left"></div>
    <div class="folio-rule right"></div>
    <div class="folio-url">www.larkmoorcover.com</div>
  </section>
</div>
</body>
</html>
```